Business Card Design

We need a business card designed for our new company. Prefer a black card with white logo & writing.

Contact Information for Business Card

Ted Galloway, address: 7-4812 Fernhollow Road, Abbotsford, BC, V3K 8R2, Office Phone: 604-712-3390, Cell: 604-947-2164, Email: ted@resinworkshub.ca

Colors

Designer to choose only greyscale colors for use in the design.

```html
<!DOCTYPE html>
<html lang="en">
<head>
<meta charset="utf-8">
<title>Resinworks Hub – Business Card</title>
<link href="https://fonts.googleapis.com/css2?family=Montserrat:wght@300;400;700;800&display=swap" rel="stylesheet">
<style>
  :root {
    --backdrop: #4a4441;
    --card-black: #111111;
    --ink-white: #ffffff;
    --ink-soft: #e6e6e6;
    --emboss: #262626;
    --grey-light: #c9c9c9;
    --grey-mid: #8d8d8d;
    --grey-dark: #555555;
  }
  * { margin: 0; padding: 0; box-sizing: border-box; }
  html, body {
    width: 1200px; height: 786px; overflow: hidden;
    background: var(--backdrop);
    font-family: "Montserrat", sans-serif;
  }
  .canvas {
    position: relative; width: 1200px; height: 786px;
    display: flex; align-items: center; justify-content: center; gap: 40px;
  }
  .card {
    position: relative; width: 525px; height: 300px;
    background: var(--card-black);
    box-shadow: 0 10px 24px rgba(0,0,0,.35);
    overflow: hidden;
  }
  /* Front */
  .brand {
    position: absolute; left: 34px; top: 34px;
    font-weight: 800; font-size: 21px; letter-spacing: .5px;
    color: var(--ink-white); text-transform: uppercase; line-height: 1;
  }
  .contact { position: absolute; left: 34px; top: 90px; color: var(--ink-soft); }
  .contact__name { font-weight: 700; font-size: 22px; color: var(--ink-white); margin-bottom: 14px; }
  .contact__address { font-weight: 300; font-size: 13px; line-height: 1.45; margin-bottom: 12px; }
  .contact__list { list-style: none; font-weight: 300; font-size: 13px; line-height: 1.6; }
  .contact__list li { display: flex; align-items: center; gap: 8px; }
  .contact__list svg { width: 11px; height: 11px; fill: var(--ink-white); flex: none; }
  .feature-disc {
    position: absolute; left: 262px; top: 40px;
    width: 220px; height: 220px; border-radius: 50%;
    background: var(--ink-white);
    display: flex; align-items: center; justify-content: center;
  }
  .feature-disc__art {
    width: 150px; height: 130px; border-radius: 6px;
    background: linear-gradient(160deg, var(--ink-white) 0%, var(--grey-light) 35%, var(--grey-mid) 65%, var(--grey-dark) 100%);
  }
  /* Back */
  .card--back { display: flex; align-items: center; justify-content: center; }
  .brand--emboss {
    position: static; font-size: 40px; color: var(--emboss); letter-spacing: 1px;
  }
</style>
</head>
<body>
<main class="canvas">
  <section class="card card--front">
    <div class="brand">Resinworks Hub</div>
    <div class="contact">
      <p class="contact__name">Ted Galloway</p>
      <p class="contact__address">7-4812 Fernhollow Road,<br>Abbotsford, BC, V3K 8R2</p>
      <ul class="contact__list">
        <li><svg viewBox="0 0 24 24"><path d="M6.6 10.8a15.1 15.1 0 0 0 6.6 6.6l2.2-2.2a1 1 0 0 1 1-.25 11.4 11.4 0 0 0 3.6.57 1 1 0 0 1 1 1V20a1 1 0 0 1-1 1A17 17 0 0 1 3 4a1 1 0 0 1 1-1h3.5a1 1 0 0 1 1 1c0 1.25.2 2.45.57 3.57a1 1 0 0 1-.25 1z"/></svg>604-712-3390</li>
        <li><svg viewBox="0 0 24 24"><path d="M17 1H7a2 2 0 0 0-2 2v18a2 2 0 0 0 2 2h10a2 2 0 0 0 2-2V3a2 2 0 0 0-2-2zm0 18H7V5h10z"/></svg>604-947-2164</li>
        <li><svg viewBox="0 0 24 24"><path d="M20 4H4a2 2 0 0 0-2 2v12a2 2 0 0 0 2 2h16a2 2 0 0 0 2-2V6a2 2 0 0 0-2-2zm0 4-8 5-8-5V6l8 5 8-5z"/></svg>ted@resinworkshub.ca</li>
      </ul>
    </div>
    <div class="feature-disc">
      <div class="feature-disc__art" role="img" aria-label="Illustration of three stacked grey floor coating layers"></div>
    </div>
  </section>
  <section class="card card--back">
    <div class="brand brand--emboss">Resinworks Hub</div>
  </section>
</main>
</body>
</html>
```